Home show booth design

We are looking at a home show booth design for our window and door company. We will have some high end doors, windows, patio door and garage door on display. 1 booth is 10x20 and 1 booth is 20x20.

Give me some design ideas and keeping in mind our product on display.

Below is our logo and i would like to keep our branding colors and i want a very attractive and high end setup to stand out from the crowd

Target Market(s)

Home owners and custom home builders

Industry/Entity Type

Windows and doors

Font styles to use
Serif

Colors

Designer to choose colors to be used in the design.

Requirements
Must have
• Back drop, small desk
Nice to have
• Large floating balloon above the booth

```html
<!DOCTYPE html>
<html lang="en">
<head>
<meta charset="utf-8">
<title>Keystone Doors &amp; Windows – Home Show Booth</title>
<link rel="stylesheet" href="https://fonts.googleapis.com/css2?family=Poppins:wght@400;500;600;700&family=Roboto:wght@700;900&display=swap">
<style>
  :root {
    --orange: #e2701f;
    --rust: #c8461c;
    --ink: #0c0c0c;
    --charcoal: #1c1c1c;
    --stage: #d0d0d0;
    --paper: #ffffff;
    --counter-top: #6f6f6f;
  }
  * { box-sizing: border-box; margin: 0; padding: 0; }
  html, body { width: 1200px; height: 840px; overflow: hidden; }
  body { background: var(--stage); position: relative; font-family: "Poppins", sans-serif; }

  /* ---------- counter wrap ---------- */
  .counter { position: absolute; left: 40px; top: 250px; width: 250px; height: 420px; }
  .counter__lid { height: 14px; background: var(--counter-top); border-radius: 4px 4px 0 0; }
  .counter__rim { height: 24px; background: var(--charcoal); }
  .counter__face { height: 230px; background: var(--paper); display: flex; flex-direction: column; align-items: center; justify-content: center; gap: 14px; }
  .counter__mark { width: 64px; height: 64px; background: var(--rust); }
  .counter__name { color: var(--rust); font-weight: 600; font-size: 23px; line-height: 1.15; text-align: center; }
  .counter__band { height: 70px; background: var(--ink); display: flex; align-items: center; justify-content: center; }
  .counter__web { font-size: 13px; font-weight: 500; color: var(--orange); }
  .counter__web b { color: var(--paper); font-weight: 500; }
  .counter__base { height: 82px; background: #262626; border-radius: 0 0 8px 8px; }

  /* ---------- backdrop ---------- */
  .backdrop { position: absolute; left: 320px; top: 60px; width: 840px; height: 720px; background: var(--paper); overflow: hidden; }
  .backdrop__floor { position: absolute; left: 0; right: 0; bottom: 0; height: 146px; background: var(--ink); }

  .brand { position: absolute; left: 0; right: 0; top: 48px; display: flex; align-items: center; justify-content: center; gap: 18px; }
  .brand__mark { width: 96px; height: 96px; background: var(--orange); }
  .brand__name { color: var(--orange); font-weight: 600; font-size: 38px; line-height: 1.1; }

  .headline { position: absolute; left: 0; right: 0; top: 176px; text-align: center; font-family: "Roboto", sans-serif; font-weight: 900; font-size: 52px; line-height: 1.2; color: var(--ink); }
  .headline__accent { color: var(--orange); }

  .services-tab { position: absolute; left: 0; top: 305px; width: 290px; height: 46px; background: var(--orange); clip-path: polygon(0 0, 262px 0, 100% 100%, 0 100%); color: var(--paper); font-size: 28px; line-height: 46px; padding-left: 30px; }
  .services-tab b { font-weight: 700; }
  .services { position: absolute; left: 30px; top: 366px; list-style: none; }
  .services li { font-size: 24px; line-height: 40px; color: var(--ink); position: relative; padding-left: 20px; }
  .services li::before { content: ""; position: absolute; left: 0; top: 18px; width: 7px; height: 7px; border-radius: 50%; background: var(--orange); }

  .quote-tab { position: absolute; left: 0; top: 546px; width: 235px; height: 30px; background: var(--orange); clip-path: polygon(0 0, 205px 0, 100% 100%, 0 100%); font-size: 18px; line-height: 30px; padding-left: 28px; color: var(--ink); font-weight: 500; }
  .contact { position: absolute; left: 30px; top: 588px; }
  .contact__phone { font-family: "Roboto", sans-serif; font-weight: 900; font-size: 42px; color: var(--paper); line-height: 1.05; }
  .contact__web { font-size: 26px; font-weight: 500; color: var(--orange); line-height: 1.3; }
  .contact__web b { color: var(--paper); font-weight: 500; }

  .gallery { position: absolute; left: 296px; top: 300px; width: 518px; height: 420px; background: var(--paper); padding: 5px; display: grid; grid-template-columns: 1fr 1fr; grid-template-rows: 140px 140px 1fr; gap: 5px; }
  .photo { display: block; }
  .photo--wide { grid-column: 1 / 3; background: linear-gradient(180deg, #5aa6e6 0%, #bfe0f5 45%, #e9dcc0 60%, #3d6c8c 100%); }
  .photo--patio { background: linear-gradient(120deg, #2b2d33 0%, #7d6c58 45%, #b7a58c 75%, #8a6a4c 100%); }
  .photo--sunroom { background: linear-gradient(160deg, #f2f3f4 0%, #d9dde0 45%, #7e8f6c 75%, #2e3f52 100%); }
  .photo--exterior { background: linear-gradient(180deg, #4b5f7a 0%, #8794a6 45%, #e5c99a 75%, #6d7b5e 100%); }
  .photo--entry { background: linear-gradient(90deg, #f4f3ef 0%, #e7e4dc 55%, #8fa8bd 80%, #f1f0ec 100%); }
</style>
</head>
<body>

  <aside class="counter">
    <div class="counter__lid"></div>
    <div class="counter__rim"></div>
    <div class="counter__face">
      <div class="counter__mark"></div>
      <div class="counter__name">Keystone<br>Doors &amp; Windows</div>
    </div>
    <div class="counter__band"><span class="counter__web">keystone<b>entry</b>.org</span></div>
    <div class="counter__base"></div>
  </aside>

  <main class="backdrop">
    <div class="backdrop__floor"></div>

    <header class="brand">
      <div class="brand__mark"></div>
      <div class="brand__name">Keystone Doors &amp; Windows</div>
    </header>

    <h1 class="headline"><span class="headline__accent">Elevate Your Home</span> With<br>Keystone Doors &amp; Windows</h1>

    <div class="services-tab">Our <b>Services</b></div>
    <ul class="services">
      <li>High end Doors</li>
      <li>Windows</li>
      <li>Patio Door and</li>
      <li>Garage Door</li>
    </ul>

    <div class="quote-tab">Get A Free Quote</div>
    <div class="contact">
      <div class="contact__phone">555.010.4477</div>
      <div class="contact__web">keystone<b>entry</b>.org</div>
    </div>

    <section class="gallery">
      <div class="photo photo--wide" role="img" aria-label="Modern home with floor-to-ceiling glass walls and a glass balcony under a blue sky"></div>
      <div class="photo photo--patio" role="img" aria-label="Family relaxing behind a large dark-framed sliding patio door"></div>
      <div class="photo photo--sunroom" role="img" aria-label="Bright sunroom lined with white-framed windows and plants"></div>
      <div class="photo photo--exterior" role="img" aria-label="Two-storey house at dusk with lit windows and garage doors"></div>
      <div class="photo photo--entry" role="img" aria-label="White entry hall with a pale blue front door and staircase"></div>
    </section>
  </main>

</body>
</html>
```